Web and Logo Design for eCommerce site

We're launching a sister brand and require a full design for the site.

The site must have an established feel and appeal to corporate and institutional buyers.
Updates

Just a note about the wireframe design:

The Search & Rescue / Coast Guard / NVDK, etc. in the header area aren't buttons or menu items, but rather just info (along the lines of a tagline).  Sort of a "who we serve" sort of thing.

Worth noting is that it's specifically geared towards LARGE BUYERS.  For example, a police force buying 200 headlamps and 85 pairs of gloves.  So they'll register + sign in and then add a bunch of items to a RFQ.

Aim for a professional, masculine design.

Target Market(s)

We will be selling outdoor gear to the military, law enforcement, fire and rescue and first responders.

Requirements
Must have
• We require:
- Logo (vector based)

Site:
- template page
* main site template, re-skinned version of our current site
* horizontal drop-down menu
- product listings page
* thumbnail view of products
- product details page
* including elements such as product image, color/size selector, descriptions and specs (again, based loosely on our current website)
- account management page
* illustrating basic data entry styles for text box, buttons, grid, etc.

The site needs to be given a responsive design, so 2 versions of each design should be presented for desktop + mobile views.

Additional funds are available if the designer is able to fully implement the designs into a responsive framework such as bootstrap.

Nice to have
• Clean, professional design similar to:

http://military.trailvexagear.com/gov/accessories/gloves.html

http://leaf.ombrivo.com/ProductFind.aspx?language=EN&category=Hardshell&subcat=Waterproof_Jackets

```html
<!DOCTYPE html>
<html lang="en">
<head>
<meta charset="utf-8">
<title>Army Parka with Liner Olive – Borealt</title>
<link href="https://fonts.googleapis.com/css2?family=Open+Sans:wght@400;600;700&display=swap" rel="stylesheet">
<style>
:root{
  --topbar:#1e242b;
  --nav:#2a3038;
  --nav-dark:#1c2127;
  --olive:#96a54e;
  --olive-dark:#5a6232;
  --page:#dde7e9;
  --white:#ffffff;
  --ink:#222;
  --red:#d0161b;
  --footer:#14100b;
  --field:#e6e6e6;
  --line:#dcdcdc;
}
*{box-sizing:border-box;margin:0;padding:0}
html,body{width:1200px;height:1196px;overflow:hidden}
body{font-family:"Open Sans",sans-serif;background:var(--page);color:var(--ink);position:relative}
.abs{position:absolute}
.topbar{left:0;top:0;width:1200px;height:34px;background:var(--topbar)}
.serve{left:110px;top:10px;font-size:10.5px;color:#e8e8e8}
.serve span{margin:0 10px}
.social{top:6px;display:flex;gap:7px;left:985px}
.social i{width:21px;height:21px;border-radius:50%;background:#fff;display:block}
.header{left:0;top:34px;width:1200px;height:84px;background:var(--white)}
.brand{left:112px;top:46px;display:flex;align-items:center;gap:10px}
.brand-mark{width:44px;height:44px;border-radius:50%;background:var(--olive-dark)}
.brand-name{font-size:38px;font-weight:700;color:var(--olive-dark);line-height:1}
.brand-tag{left:187px;top:91px;font-size:10.5px;letter-spacing:1px;color:#333}
.contact{left:782px;top:66px;font-size:14px;color:#777;display:flex;align-items:center;gap:8px}
.cart{left:954px;top:66px;font-size:14px;color:#777;display:flex;align-items:center;gap:8px}
.mainnav{left:110px;top:118px;width:980px;height:42px;background:linear-gradient(var(--nav),var(--nav-dark));display:flex;align-items:center;padding-left:21px}
.mainnav a{font-size:13.8px;color:var(--olive);text-decoration:none;margin-right:28px;text-transform:uppercase}
.mainnav a.active{color:#fff}
.search{left:1051px;top:125px;width:26px;height:25px;background:var(--olive);display:flex;align-items:center;justify-content:center}
.panel{left:110px;top:169px;width:980px;height:662px;background:var(--white)}
.crumbs{left:128px;top:189px;font-size:12.5px;color:#222}
.crumbs a{color:#222;text-decoration:underline}
.crumbs b{font-weight:400;margin:0 5px}
.photo-frame{left:126px;top:231px;width:438px;height:422px;border:1px solid var(--line)}
.photo{left:146px;top:243px;width:404px;height:386px;background:radial-gradient(ellipse 55% 52% at 50% 48%,#b39a72,#9c8560 80%,#fff 100%)}
.thumb{top:670px;width:66px;height:63px;border:1px solid var(--line);background:radial-gradient(ellipse 48% 44% at 50% 50%,#a88e66 75%,#fff 100%)}
.arrow{top:692px}
.title{left:599px;top:222px;font-size:26px;font-weight:400;color:#111}
.desc{left:599px;top:270px;width:450px;font-size:12.3px;line-height:20px;color:#333}
.more{left:599px;top:360px;font-size:12px;color:var(--olive-dark)}
.more u{color:#7d8a36}
.price-label{top:408px;font-size:15.5px}
.price{top:425px;font-size:28px;font-weight:700}
.retail{color:var(--olive-dark)}
.yours{color:var(--red)}
.vline{top:408px;width:1px;height:56px;background:var(--line)}
.ship{left:917px;top:407px;font-size:11.8px;line-height:20px;color:#222}
.opt-label{left:598px;font-size:15px;color:#222}
.select{left:731px;width:290px;height:36px;border:1px solid #c9c9c9;font-size:12.5px;color:#222;padding:8px 12px}
.select i{position:absolute;right:10px;top:9px;width:16px;height:16px;border:1px solid #888;background:#f2f2f2}
.select i::after{content:"";position:absolute;left:3px;top:5px;border:4px solid transparent;border-top:5px solid #333}
.rfq{left:598px;top:676px;width:139px;height:45px;background:linear-gradient(#dc1e22,#b5100f);border-radius:3px;color:#fff;font-size:18px;font-weight:600;display:flex;align-items:center;justify-content:center}
.rule{left:593px;top:748px;width:439px;height:1px;background:#e6e6e6}
.share{top:781px;display:flex;align-items:center;gap:3px;font-size:11px}
.share b{border:1px solid #ccc;border-radius:2px;padding:1px 6px;font-weight:700;color:#333;background:#f6f6f6}
.share span{border:1px solid #ccc;padding:1px 4px;font-size:10px;color:#555}
.footer{left:0;top:904px;width:1200px;height:292px;background:var(--footer);color:#ddd}
.fhead{top:939px;font-size:16.3px;font-weight:600;color:#fff}
.flist{top:985px;font-size:12.8px;line-height:22px;list-style:none;color:#d8d8d8}
.ftext{left:543px;top:987px;width:260px;font-size:12.5px;line-height:18px;color:#bbb}
.email{left:543px;top:1042px;width:193px;height:38px;background:#fff;font-size:13px;color:#aaa;padding:10px}
.enter{left:735px;top:1042px;width:61px;height:38px;background:#ccc;font-size:15px;color:#333;display:flex;align-items:center;justify-content:center}
.qf{left:915px;width:220px;background:var(--field);font-size:12px;color:#333;padding:5px 11px}
.submit{left:913px;top:1154px;width:86px;height:24px;background:var(--olive);color:#fff;font-size:12px;display:flex;align-items:center;justify-content:center}
</style>
</head>
<body>
<div class="abs topbar"></div>
<div class="abs serve">SEARCH &amp;RECUE<span>|</span>COAST GUARD<span>|</span>NVDK<span>|</span>FIRE<span>|</span>MILIATRY<span>|</span>LAW ENFORCEMENT</div>
<div class="abs social"><i></i><i></i><i></i><i></i></div>

<div class="abs header"></div>
<div class="abs brand"><div class="brand-mark"></div><div class="brand-name">Borealt</div></div>
<div class="abs brand-tag">NORTHERN FIELD GEAR SUPPLY</div>
<div class="abs contact">
  <svg width="18" height="18" viewBox="0 0 24 24"><path d="M6.6 10.8a15 15 0 006.6 6.6l2.2-2.2c.3-.3.7-.4 1-.2 1.1.4 2.3.6 3.6.6.6 0 1 .4 1 1V20c0 .6-.4 1-1 1A17 17 0 013 4c0-.6.4-1 1-1h3.5c.6 0 1 .4 1 1 0 1.3.2 2.5.6 3.6.1.3 0 .7-.2 1z" fill="#999"/></svg>
  Call (+) 0800.555.019
</div>
<div class="abs cart">
  <svg width="18" height="16" viewBox="0 0 18 16"><path d="M1 6h16l-2 9H3z M5 6l4-5 4 5" fill="none" stroke="#888" stroke-width="1.6"/></svg>
  (0 item) - $0.00 <span style="font-size:10px">▼</span>
</div>

<nav class="abs mainnav">
  <a class="active">Rescue Gear</a><a>Footwear</a><a>Clothing</a><a>Tents Mats Sleeping Bags</a><a>Camping Gear</a><a>Snow Sports</a><a>Brand’s</a>
</nav>
<div class="abs search"><svg width="14" height="14" viewBox="0 0 14 14"><circle cx="6" cy="6" r="4.3" fill="none" stroke="#fff" stroke-width="2"/><path d="M9 9l4 4" stroke="#fff" stroke-width="2.2"/></svg></div>

<main class="abs panel"></main>
<div class="abs crumbs"><a>Rescue Gear</a><b>&gt;</b><a>Helmet</a><b>&gt;</b><a>Maze Helmet</a></div>

<div class="abs photo-frame"></div>
<div class="abs photo" role="img" aria-label="Product photo of a tan long-sleeve field shirt"></div>
<svg class="abs arrow" style="left:195px" width="10" height="14"><path d="M9 0v14L0 7z" fill="#4a5230"/></svg>
<div class="abs thumb" style="left:229px" role="img" aria-label="Shirt thumbnail, front"></div>
<div class="abs thumb" style="left:302px" role="img" aria-label="Shirt thumbnail, alternate view"></div>
<div class="abs thumb" style="left:375px" role="img" aria-label="Shirt thumbnail, detail"></div>
<svg class="abs arrow" style="left:462px" width="10" height="14"><path d="M0 0v14L10 7z" fill="#4a5230"/></svg>

<h1 class="abs title">Army Parka with Liner Olive</h1>
<p class="abs desc">All the actual measurements given on the site as "armpit to armpit x 2" refer to the measurements of the garment and not the size it will fit.<br>The best way of checking if an item will fit is to measure a similar garment you have which fits well and compare the measurements.</p>
<div class="abs more">+ <u>more</u></div>

<div class="abs price-label retail" style="left:600px">RETAIL PRICE</div>
<div class="abs price retail" style="left:599px">$199.99</div>
<div class="abs vline" style="left:717px"></div>
<div class="abs price-label yours" style="left:738px">YOUR PRICE LEVEL</div>
<div class="abs price yours" style="left:737px">$150.99</div>
<div class="abs vline" style="left:894px"></div>
<div class="abs ship">Free Canada Shipping<br>In Stock<br>Ship in 24 hours</div>

<div class="abs opt-label" style="top:517px">Size:</div>
<div class="abs select" style="top:508px">XL<i></i></div>
<div class="abs opt-label" style="top:562px">Color:</div>
<div class="abs select" style="top:553px">Olive Green<i></i></div>
<div class="abs opt-label" style="top:612px">Quantity:</div>
<div class="abs select" style="top:602px">1<i></i></div>

<div class="abs rfq">ADD TO RFQ</div>
<div class="abs rule"></div>
<div class="abs share" style="left:595px"><b>Share</b><span>0</span></div>
<div class="abs share" style="left:685px"><b>Post</b><span>0</span></div>
<div class="abs share" style="left:775px"><b>+1</b><span>0</span></div>
<div class="abs share" style="left:843px"><b>Save</b></div>

<footer class="abs footer"></footer>
<h3 class="abs fhead" style="left:159px">Navigation</h3>
<ul class="abs flist" style="left:159px"><li>Rescue Gear</li><li>Footwear</li><li>Clothing</li><li>Tents Mats</li><li>Sleeping Bags</li><li>Camping Gear</li><li>Snow Sports</li><li>Brands</li></ul>
<h3 class="abs fhead" style="left:358px">Products</h3>
<ul class="abs flist" style="left:358px"><li>Rescue Gear</li><li>Footwear</li><li>Clothing</li><li>Tents Mats</li><li>Sleeping Bags</li><li>Camping Gear</li><li>Snow Sports</li><li>Brands</li></ul>
<h3 class="abs fhead" style="left:543px">Get informed for our Special offers</h3>
<p class="abs ftext">Get the best and most interesting discount offers via email.</p>
<div class="abs email">you@example.com</div>
<div class="abs enter">Enter</div>
<h3 class="abs fhead" style="left:914px">Quick Contact</h3>
<div class="abs qf" style="top:980px;height:25px">Name:</div>
<div class="abs qf" style="top:1012px;height:25px">Email:</div>
<div class="abs qf" style="top:1044px;height:25px">Phone:</div>
<div class="abs qf" style="top:1077px;height:67px">Message:</div>
<div class="abs submit">SUBMIT</div>
</body>
</html>
```